Business Cards Design for the electrical wholesaler: clean bold dynamic :)

We need a business card design that would follow our latest brand guidelines. As an electrical wholesaler we want to bring a fresh look and feel into the industry. The design should be clean bold and dynamic. It should come alive with the renewed energy of our green colour. Our grey colour should keep things balanced and complement the notion of maturity and responsibility. We employ Lato as a corporate font however are not bound by this font and we’re open to interpretation here.

Target Market(s)

Electrical contractors

Industry/Entity Type

Business

Contact Information for Business Card

Logo
Name & Surname: Halyna Dorosh
Job Title: Director of Marketing
Email: halya.dorosh@quillmail.example
Cell phone: XXX.XXX.XXXX
Address: 20517 - 87 Ave. Edmonton, AB, Canada. T6K 4N8
Business Phone: 780.555.0184
Website: www.brovix.example

Font styles to use
Other font styles liked:
• Lato

Requirements
Must have
• Logo & website
Nice to have
• Brand elements - some of them you may find in the attached Brand Guidelines (e.g. three lines on the background signifying "W")

```html
<!DOCTYPE html>
<html lang="en">
<head>
<meta charset="utf-8">
<title>Brovix business card</title>
<link href="https://fonts.googleapis.com/css2?family=Roboto:wght@400;500;700&display=swap" rel="stylesheet">
<style>
  :root {
    --green: #8cc63f;
    --grey: #4d4d4f;
    --ink: #3a3a3c;
    --white: #ffffff;
    --backdrop: #1b1b1c;
  }
  * { box-sizing: border-box; margin: 0; padding: 0; }
  html, body { width: 1200px; height: 963px; overflow: hidden; }
  body {
    background: var(--backdrop);
    font-family: "Roboto", sans-serif;
    display: flex;
    flex-direction: column;
    align-items: center;
    justify-content: center;
    gap: 60px;
  }
  .card {
    position: relative;
    width: 640px;
    height: 366px;
    border-radius: 18px;
    overflow: hidden;
  }
  /* Front */
  .card--front { background: var(--white); color: var(--ink); }
  .card__wave { position: absolute; inset: 0; width: 100%; height: 100%; }
  .brand {
    position: absolute;
    left: 44px;
    top: 108px;
    display: flex;
    align-items: center;
    gap: 14px;
  }
  .brand__mark { width: 30px; height: 30px; background: var(--green); }
  .brand__name { font-size: 54px; font-weight: 500; color: var(--grey); letter-spacing: -1px; line-height: 1; }
  .divider {
    position: absolute;
    left: 318px;
    top: 70px;
    width: 2px;
    height: 170px;
    background: var(--green);
  }
  .contact {
    position: absolute;
    left: 342px;
    top: 70px;
    font-size: 13px;
    line-height: 1.45;
  }
  .contact__name { font-size: 24px; font-weight: 500; color: var(--green); line-height: 1.1; }
  .contact__title { font-size: 15px; color: var(--ink); margin-bottom: 10px; }
  .contact__address { width: 260px; margin-bottom: 8px; }
  .contact__row { display: flex; align-items: center; gap: 8px; }
  .contact__icon { width: 11px; height: 11px; flex: none; }
  .accent { color: var(--green); }
  /* Back */
  .card--back { background: var(--green); color: var(--white); }
  .card--back .brand { left: 50%; top: 120px; transform: translateX(-50%); }
  .card--back .brand__mark { background: var(--white); width: 40px; height: 40px; }
  .card--back .brand__name { color: var(--white); font-size: 84px; }
  .card__web {
    position: absolute;
    left: 0; right: 0;
    bottom: 56px;
    text-align: center;
    font-size: 16px;
    letter-spacing: 0.5px;
  }
</style>
</head>
<body>

  <section class="card card--front">
    <svg class="card__wave" viewBox="0 0 640 366" preserveAspectRatio="none" aria-hidden="true">
      <path d="M0 236 C 150 236, 220 300, 330 330 S 560 352, 640 352 L 640 366 L 0 366 Z" fill="var(--green)"/>
      <path d="M0 228 C 150 230, 220 292, 330 322 S 560 346, 640 346" fill="none" stroke="var(--grey)" stroke-width="6"/>
      <path d="M0 241 C 150 241, 220 306, 330 336 S 560 358, 640 358 L 640 366 L 0 366 Z" fill="var(--green)"/>
    </svg>

    <div class="brand">
      <span class="brand__mark"></span>
      <span class="brand__name">Brovix</span>
    </div>

    <div class="divider"></div>

    <div class="contact">
      <p class="contact__name">Halyna Dorosh</p>
      <p class="contact__title">Founder</p>
      <p class="contact__address">20517 - 87 Ave. Edmonton, AB, Canada. T6K 4N8</p>
      <p class="contact__row">
        <svg class="contact__icon" viewBox="0 0 12 12"><path d="M2.5 1 L4.5 1 L5.3 3.6 L4 4.6 C4.6 6 5.9 7.4 7.4 8 L8.4 6.7 L11 7.5 L11 9.5 C11 10.3 10.3 11 9.5 11 C5 11 1 7 1 2.5 C1 1.7 1.7 1 2.5 1 Z" fill="var(--green)"/></svg>
        780.555.0184
      </p>
      <p class="contact__row">
        <svg class="contact__icon" viewBox="0 0 12 12"><rect x="1" y="2.5" width="10" height="7" rx="1" fill="none" stroke="var(--green)" stroke-width="1.3"/><path d="M1.5 3 L6 6.5 L10.5 3" fill="none" stroke="var(--green)" stroke-width="1.3"/></svg>
        halya.dorosh@quillmail.example
      </p>
      <p class="contact__row">
        <svg class="contact__icon" viewBox="0 0 12 12"><circle cx="6" cy="6" r="5" fill="none" stroke="var(--green)" stroke-width="1.2"/><path d="M1 6 H11 M6 1 C3.5 3.5 3.5 8.5 6 11 M6 1 C8.5 3.5 8.5 8.5 6 11" fill="none" stroke="var(--green)" stroke-width="1"/></svg>
        www.<span class="accent">brovix</span>.example
      </p>
    </div>
  </section>

  <section class="card card--back">
    <div class="brand">
      <span class="brand__mark"></span>
      <span class="brand__name">Brovix</span>
    </div>
    <p class="card__web">www.brovix.example</p>
  </section>

</body>
</html>
```